Modern Banner and Window Decal Design For Law Firm Lawyer

We are looking for three modern and sophisticated banner design and window decal for our law firm.

Banner measurements/types:

1) Height: 130 cm Width: 160 cm (Outdoor banner)
2) Height: 200 cm Width: 85 cm (Pull up/retractable indoor banner)

Window Decal:
3) Height: 70cm width 70cm

Our law firm is based in Melbourne, Australia and we deal with property law mostly.

We prefer a white background with classic text in black or grey. We would also like a dash of colour so please use a green, blue or aqua colour palette that is consistent with our logo. Vector attached. A nice photo of property, Melbourne city viee, or family home would be nice.

We do not want any law related images - scales of justice, gavel or the like.

Our ultimate goal is to communicate that the firm is modern, professional and knowledgeable

We would like the following:

1. Our logo
2. Our services: - Property Law - Wills - Powers of Attorney - Probate - Estate Administration - Consultancy & Agency
3. Phone number
4. Web Address

5. For pull up/retractable banner we would also like the following text:

We use the latest digital technology and fixed-fees to provide fast and affordable legal advice that is easy to understand.

For privacy reasons, we will provide business details once we have decided on the winner.

We will monitor entries closely and promise to provide feedback and guidance on each entry.

Thank you very much for considering this project.

Target Market(s)

General public, professionals, lawyers and conveyancers

Industry/Entity Type

Law Firm

Font styles to use
Sans Serif

Colors
0393ce
34a6d7
0456a4
3176b5
acd037
33b8a4
86cfc6
00a990
9ccb3b

Requirements
Must have
• 1. Our logo
• 2. Our services: - Property Law - Wills - Powers of Attorney - Probate & Estate Administration - Consultancy & Agency
• 3. Phone number
• 4. Web Address
Nice to have
• Picture of Melbourne, Australia city ; property/buildings/lawyers
Should not have
• We do not want any law related images - scales of justice, gavel or the like.

```html
<!DOCTYPE html>
<html lang="en">
<head>
<meta charset="utf-8">
<title>Carrow Lawyers – Pull-up Banner</title>
<link href="https://fonts.googleapis.com/css2?family=Oswald:wght@500&family=Roboto:wght@400;700&family=Roboto+Condensed:wght@700&display=swap" rel="stylesheet">
<style>
  :root {
    --stage: #e9ebee;
    --paper: #ffffff;
    --ink: #111418;
    --grey: #6b6f74;
    --navy: #0456a4;
    --blue: #3176b5;
    --teal: #33b8a4;
    --aqua: #86cfc6;
    --photo-light: #c9d6e6;
    --photo-mid: #7f9abb;
    --photo-dark: #2e4a72;
  }
  * { margin: 0; padding: 0; box-sizing: border-box; }
  html, body { width: 1200px; height: 1000px; overflow: hidden; }
  body { background: var(--stage); position: relative; font-family: "Roboto", sans-serif; }

  .banner {
    position: absolute; left: 410px; top: 32px;
    width: 380px; height: 936px;
    background: var(--paper);
    box-shadow: 0 4px 18px rgba(0,0,0,.12);
    overflow: hidden;
  }
  .banner__art { position: absolute; left: 0; top: 0; width: 380px; height: 680px; }

  .services-tag {
    position: absolute; left: 90px; top: 478px;
    width: 198px; height: 30px;
    background: var(--navy); color: var(--paper);
    border-radius: 6px;
    font: 700 19px/30px "Roboto", sans-serif;
    text-align: center; letter-spacing: .3px;
  }
  .services { position: absolute; left: 53px; top: 522px; list-style: none; }
  .services li {
    position: relative; padding-left: 22px; margin-bottom: 8px;
    font: 500 26px/29px "Oswald", sans-serif;
    color: var(--ink); text-transform: uppercase; letter-spacing: -.2px;
  }
  .services li::before {
    content: ""; position: absolute; left: 0; top: 8px;
    width: 12px; height: 12px; background: var(--blue);
  }

  .brand { position: absolute; left: 55px; top: 760px; display: flex; align-items: center; gap: 14px; }
  .brand__dot { width: 72px; height: 72px; border-radius: 50%; background: var(--aqua); }
  .brand__name {
    font: 400 24px/28px "Roboto", sans-serif; color: var(--grey);
    letter-spacing: .5px; text-transform: uppercase;
  }

  .contact { position: absolute; left: 0; width: 380px; top: 860px; text-align: center; }
  .contact__phone {
    display: inline-flex; align-items: center; gap: 8px;
    font: 700 28px/32px "Roboto Condensed", sans-serif; color: var(--ink);
  }
  .contact__icon { width: 24px; height: 24px; }
  .contact__web { font: 700 14px/18px "Roboto", sans-serif; color: var(--ink); margin-top: 2px; }

  .rule { position: absolute; top: 916px; height: 7px; }
  .rule--navy { left: 0; width: 220px; background: var(--navy); }
  .rule--teal { left: 226px; width: 154px; background: var(--teal); }
</style>
</head>
<body>
  <main class="banner">
    <svg class="banner__art" viewBox="0 0 380 680" width="380" height="680">
      <defs>
        <linearGradient id="cityTone" x1="0" y1="0" x2="1" y2="1">
          <stop offset="0" stop-color="var(--photo-light)"/>
          <stop offset=".55" stop-color="var(--photo-mid)"/>
          <stop offset="1" stop-color="var(--photo-dark)"/>
        </linearGradient>
      </defs>
      <polygon role="img" aria-label="Night city skyline with tall towers and light trails along a street, in cool blue tones"
               points="0,0 258,0 380,56 380,672 0,356" fill="url(#cityTone)"/>
      <polygon class="corner-accent" points="262,0 358,0 358,40" fill="var(--teal)"/>
    </svg>

    <div class="services-tag">OUR SERVICES:</div>
    <ul class="services">
      <li>Property Law</li>
      <li>Wills</li>
      <li>Powers of Attorney</li>
      <li>Probate &amp; Estate<br>Administration</li>
      <li>Consultancy &amp; Agency</li>
    </ul>

    <div class="brand">
      <span class="brand__dot"></span>
      <span class="brand__name">Carrow<br>Lawyers</span>
    </div>

    <div class="contact">
      <div class="contact__phone">
        <svg class="contact__icon" viewBox="0 0 24 24" aria-hidden="true">
          <rect width="24" height="24" rx="5" fill="var(--navy)"/>
          <path d="M8.2 5.5l2 .2 1 3-1.4 1.2a8 8 0 0 0 4.3 4.3l1.2-1.4 3 1 .2 2c0 .9-.8 1.7-1.8 1.6C10.9 17 7 13.1 6.6 7.3 6.5 6.3 7.3 5.5 8.2 5.5z" fill="#fff"/>
        </svg>
        555-0142-7788
      </div>
      <div class="contact__web">www.carrowlawyers.com</div>
    </div>

    <div class="rule rule--navy"></div>
    <div class="rule rule--teal"></div>
  </main>
</body>
</html>
```